KRT Flyer to attract applicants 11x17

Lantern Stagehand Collective provides crew for local concerts, filming, theater, and corporate events.
The flyer will be posted on bulletin boards at colleges with theater programs.
Our primary venues are historic theaters in downtown LA
Need a 11x17 poster to attract potential applicants/crew
I have attached a poster that one of our staff made that has all if the relevant info - but i know the poster can look much better than that. I have also attached many images and our logo. It is not necessary to use all of the images, or any of them. The two images of the theater interiors are the venues we operate so they would be the first to include. I can send additional info or images upon request. Thank you

Industry/Entity Type

Entertainment

Requirements
Must have
• APPLY@KRTCREW.EXAMPLE

```html
<!DOCTYPE html>
<html lang="en">
<head>
<meta charset="utf-8">
<title>Lantern Stagehand Collective – Open Positions</title>
<link rel="stylesheet" href="https://fonts.googleapis.com/css2?family=Exo+2:wght@300;400;700;800;900&display=swap">
<style>
  :root {
    --page: #ececec;
    --white: #ffffff;
    --brand-blue: #2452a8;
    --stripe-blue: #1f6fc0;
    --stripe-light: #4aa6e6;
    --yellow: #f0b71a;
    --green: #b7d534;
    --orange: #ee4420;
    --ink: #1c1c2a;
    --grey-mark: #9a9a9a;
  }
  * { margin: 0; padding: 0; box-sizing: border-box; }
  html, body {
    width: 1200px; height: 1200px; overflow: hidden;
    background: var(--page);
    font-family: "Exo 2", sans-serif;
  }
  .poster {
    position: absolute; left: 231px; top: 30px;
    width: 738px; height: 1140px; overflow: hidden;
    background: var(--white);
  }
  .poster-art { position: absolute; inset: 0; }
  .brand {
    position: absolute; left: 136px; top: 52px;
    display: flex; align-items: center; gap: 14px;
  }
  .brand-dot {
    width: 52px; height: 52px; border-radius: 50%;
    background: var(--grey-mark);
  }
  .brand-name {
    font-weight: 700; font-size: 27px; color: var(--brand-blue);
    letter-spacing: 0.2px;
  }
  .headline {
    position: absolute; left: 44px; top: 168px;
    color: var(--white); font-weight: 900;
    font-size: 100px; line-height: 96px; letter-spacing: 1px;
  }
  .lead {
    position: absolute; left: 48px; top: 480px;
    color: var(--white); font-weight: 300;
    font-size: 50px; line-height: 50px;
  }
  .lead strong { color: var(--yellow); font-weight: 800; }
  .roster {
    position: absolute; left: 48px; top: 658px;
    color: var(--white); font-weight: 800;
    font-size: 37px; line-height: 37px;
  }
  .roster strong { color: var(--green); font-weight: 800; }
  .apply-tab {
    position: absolute; left: 49px; top: 895px;
    width: 214px; height: 26px;
    background: var(--yellow);
    clip-path: polygon(0 0, 91% 0, 100% 100%, 0 100%);
    color: var(--ink); font-weight: 400; font-size: 19px;
    line-height: 26px; padding-left: 16px;
  }
  .apply-email {
    position: absolute; left: 48px; top: 929px;
    color: var(--white); font-weight: 800; font-size: 24px;
    white-space: nowrap;
  }
  .divider {
    position: absolute; left: 48px; top: 995px;
    width: 67px; height: 7px; background: var(--white);
  }
  .info-label {
    position: absolute; left: 48px; top: 1028px;
    color: var(--white); font-weight: 300; font-size: 21px;
  }
  .info-url {
    position: absolute; left: 48px; top: 1057px;
    color: var(--white); font-weight: 800; font-size: 25px;
    white-space: nowrap;
  }
</style>
</head>
<body>
  <main class="poster">
    <svg class="poster-art" width="738" height="1140" viewBox="0 0 738 1140" xmlns="http://www.w3.org/2000/svg">
      <defs>
        <linearGradient id="band-fill" x1="0" y1="0" x2="1" y2="0">
          <stop offset="0" stop-color="#2459ab"/>
          <stop offset="1" stop-color="#2c3c9c"/>
        </linearGradient>
        <linearGradient id="night-fill" x1="0" y1="0" x2="0.6" y2="1">
          <stop offset="0" stop-color="#cf2030"/>
          <stop offset="0.35" stop-color="#3a2358"/>
          <stop offset="0.7" stop-color="#2a3a98"/>
          <stop offset="1" stop-color="#2e45b0"/>
        </linearGradient>
        <linearGradient id="hall-fill" x1="0" y1="0" x2="0" y2="1">
          <stop offset="0" stop-color="#3a2a3a"/>
          <stop offset="0.25" stop-color="#c89a4a"/>
          <stop offset="0.5" stop-color="#8a6a58"/>
          <stop offset="0.75" stop-color="#b2303a"/>
          <stop offset="1" stop-color="#6a1420"/>
        </linearGradient>
        <linearGradient id="stage-fill" x1="0" y1="0" x2="0" y2="1">
          <stop offset="0" stop-color="#5a3aa0"/>
          <stop offset="0.45" stop-color="#c0704a"/>
          <stop offset="1" stop-color="#2a1438"/>
        </linearGradient>
        <linearGradient id="cv-fill" x1="0" y1="0" x2="1" y2="1">
          <stop offset="0" stop-color="#e84a6a"/>
          <stop offset="1" stop-color="#dde3ee"/>
        </linearGradient>
      </defs>

      <rect class="night-backdrop" x="0" y="370" width="738" height="770" fill="url(#night-fill)" role="img" aria-label="Downtown city skyline at night"/>
      <rect class="headline-band" x="0" y="157" width="738" height="275" fill="url(#band-fill)"/>

      <polygon class="accent-stripe" points="725,0 738,0 738,205 465,732 441,732" fill="var(--stripe-blue)"/>

      <polygon class="venue-photo-hall" points="738,205 738,866 550,798 404,1140 395,1140 415,1060 420,880 430,790 465,732" fill="url(#hall-fill)" role="img" aria-label="Historic theater auditorium with chandelier and red seating"/>

      <polygon class="photo-frame" points="550,798 738,866 738,878 560,815 416,1140 404,1140" fill="var(--stripe-light)"/>
      <polygon class="venue-photo-stage" points="560,815 738,878 738,1140 416,1140" fill="url(#stage-fill)" role="img" aria-label="Ornate historic theater stage and dome"/>

      <polygon class="accent-corner" points="375,1140 395,1085 420,1068 404,1140" fill="var(--orange)"/>

      <g class="resume-icon" role="img" aria-label="Resume document icon" transform="rotate(20 132 836)">
        <rect x="104" y="800" width="58" height="74" rx="4" fill="url(#cv-fill)"/>
      </g>
    </svg>

    <div class="brand">
      <span class="brand-dot"></span>
      <span class="brand-name">Lantern Stagehand Collective</span>
    </div>

    <h1 class="headline">HAS OPEN<br>POSITIONS</h1>

    <p class="lead">WE ARE LOOKING<br>FOR <strong>TALENTED<br>TECHNICIANS</strong></p>

    <p class="roster">TO ADD TO OUR<br>ROSTER OF <strong>SKILLED<br>PROFESSIONALS.</strong></p>

    <div class="apply-tab">Send Resume to:</div>
    <p class="apply-email">APPLY@KRTCREW.EXAMPLE</p>

    <div class="divider"></div>

    <p class="info-label">for more information:</p>
    <p class="info-url">WWW.KRTCREW.EXAMPLE</p>
  </main>
</body>
</html>
```